Indy Film Production Company/Studio

We need a business card designed from an existing logo. We are a digital studio/production company that caters to creating genre entertainment, like Action, Horror, and martial arts. The card along with the logo will be used to Brand the company from letter heads to banners. The design will also be used for postcards and Brochures. It should be professional and masculine.
Updates

Thank you to all the designers who have participated. I'm narrowing down who it will be. Thank you again.

Target Market(s)

Investors, Networks, Producers, and actors

Industry/Entity Type

Film Production

Contact Information for Business Card

Teodoro Valbuena
Producer/Writer/Director
www.kestrelpicturehouse.example

Requirements
Must have
• Website address, plain circle with kestrelpicturehouse and plain square with @kestrelpictures possibly in the back of the card.
Nice to have
• Logline of Company: Follow The Action.

```html
<!DOCTYPE html>
<html lang="en">
<head>
<meta charset="utf-8">
<title>Kestrel Picture House – Business Card</title>
<link href="https://fonts.googleapis.com/css2?family=Open+Sans:wght@400;600;800&display=swap" rel="stylesheet">
<style>
  :root {
    --brand-red: #ec1c24;
    --card-white: #ffffff;
    --backdrop: #ecebe8;
    --shadow: rgba(0, 0, 0, 0.18);
  }
  * { box-sizing: border-box; margin: 0; padding: 0; }
  html, body {
    width: 1200px;
    height: 900px;
    overflow: hidden;
    background: var(--backdrop);
    font-family: "Open Sans", sans-serif;
  }
  .canvas { position: relative; width: 1200px; height: 900px; }

  .card {
    position: absolute;
    overflow: hidden;
    box-shadow: 0 6px 18px var(--shadow);
  }
  .card-front { left: 77px; top: 33px; width: 590px; height: 365px; background: var(--card-white); }
  .card-back  { left: 388px; top: 505px; width: 567px; height: 352px; background: var(--brand-red); }

  .front-band { position: absolute; inset: 0; }

  .wordmark {
    position: absolute;
    left: 0; right: 0;
    text-align: center;
    font-weight: 800;
    line-height: 1;
    letter-spacing: 0.02em;
  }
  .wordmark-main { display: block; font-size: 64px; }
  .wordmark-sub  { display: block; font-size: 22px; margin-top: 8px; letter-spacing: 0.08em; }
  .card-front .wordmark { top: 50px; color: var(--brand-red); padding-left: 16px; }
  .card-back  .wordmark { top: 112px; color: var(--card-white); }

  .person {
    position: absolute;
    right: 317px; top: 262px;
    text-align: right;
    color: var(--card-white);
  }
  .person-name  { font-size: 19px; font-weight: 600; line-height: 26px; }
  .person-title { font-size: 14.5px; font-weight: 400; line-height: 22px; }

  .contact-list {
    position: absolute;
    left: 292px; top: 251px;
    list-style: none;
    color: var(--card-white);
    font-size: 15px;
    line-height: 21px;
  }
  .contact-list li { display: flex; align-items: center; gap: 13px; }
  .contact-list svg { width: 12px; height: 12px; fill: var(--card-white); flex: none; }

  .address {
    position: absolute;
    left: 104px; top: 330px;
    color: var(--card-white);
    font-size: 15px;
  }

  .social-row {
    position: absolute;
    left: 0; right: 0; top: 292px;
    display: flex;
    justify-content: center;
    gap: 28px;
    list-style: none;
    color: var(--card-white);
    font-size: 13px;
    line-height: 18px;
  }
  .social-row li { display: flex; align-items: center; gap: 8px; }
  .social-dot { width: 14px; height: 14px; background: var(--card-white); flex: none; }
  .social-dot.round { border-radius: 50%; }
</style>
</head>
<body>
<div class="canvas">

  <section class="card card-front" aria-label="Business card front">
    <svg class="front-band" width="590" height="365" viewBox="0 0 590 365" aria-hidden="true">
      <polygon points="0,200 410,200 418,192 590,192 590,365 0,365" fill="var(--brand-red)"/>
      <polyline points="0,227 383,227 415,193" fill="none" stroke="var(--card-white)" stroke-width="2.5"/>
    </svg>

    <div class="wordmark">
      <span class="wordmark-main">KESTREL</span>
      <span class="wordmark-sub">PICTURE HOUSE</span>
    </div>

    <div class="person">
      <p class="person-name">Teodoro Valbuena</p>
      <p class="person-title">Producer/Writer/Director</p>
    </div>

    <ul class="contact-list">
      <li>
        <svg viewBox="0 0 24 24"><path d="M6.6 10.8a15.1 15.1 0 0 0 6.6 6.6l2.2-2.2c.3-.3.7-.4 1-.2 1.1.4 2.3.6 3.6.6.6 0 1 .4 1 1V20c0 .6-.4 1-1 1C10.6 21 3 13.4 3 4c0-.6.4-1 1-1h3.5c.6 0 1 .4 1 1 0 1.3.2 2.5.6 3.6.1.3 0 .7-.2 1z"/></svg>
        <span>044-555 010 789</span>
      </li>
      <li>
        <svg viewBox="0 0 24 24"><path d="M2 5h20v14H2z"/><path d="M3 6l9 7 9-7v-1H3z" fill="var(--brand-red)"/></svg>
        <span>info@kestrelpicture.example</span>
      </li>
      <li>
        <svg viewBox="0 0 24 24"><path d="M12 2a10 10 0 1 0 0 20 10 10 0 0 0 0-20zm6.9 6h-3a15 15 0 0 0-1.3-3.9A8 8 0 0 1 18.9 8zM12 4c.8 1.2 1.5 2.5 1.9 4h-3.8c.4-1.5 1.1-2.8 1.9-4zM4.3 14a8 8 0 0 1 0-4h3.4a16 16 0 0 0 0 4zm.8 2h3a15 15 0 0 0 1.3 3.9A8 8 0 0 1 5.1 16zm3-8h-3a8 8 0 0 1 4.3-3.9C8.8 5.3 8.4 6.6 8.1 8zM12 20c-.8-1.2-1.5-2.5-1.9-4h3.8c-.4 1.5-1.1 2.8-1.9 4zm2.3-6H9.7a14 14 0 0 1 0-4h4.6a14 14 0 0 1 0 4zm.3 5.9c.6-1.2 1-2.5 1.3-3.9h3a8 8 0 0 1-4.3 3.9zm1.7-5.9a16 16 0 0 0 0-4h3.4a8 8 0 0 1 0 4z"/></svg>
        <span>www.kestrelpicturehouse.example</span>
      </li>
    </ul>

    <p class="address">12345, Address Goes Here Country Name, 123456.</p>
  </section>

  <section class="card card-back" aria-label="Business card back">
    <div class="wordmark">
      <span class="wordmark-main">KESTREL</span>
      <span class="wordmark-sub">PICTURE HOUSE</span>
    </div>

    <ul class="social-row" aria-label="Social profiles">
      <li><span class="social-dot round" aria-hidden="true"></span><span>kestrelpicturehouse</span></li>
      <li><span class="social-dot" aria-hidden="true"></span><span>@kestrelpictures</span></li>
    </ul>
  </section>

</div>
</body>
</html>
```